​Silver Harbor Rhythm provides personal, friendly service in a fun and high energy environment. We are based in Vermont.

We would like a card that appeals to a wide range of audiences as we do a wide range of events. Please feel free to check out our website silverharborrhythm.net for inspiration.

Target Market(s)

weddings, corporate, birthday parties, colleges

Industry/Entity Type

Business

Contact Information for Business Card

Silver Harbor Rhythm
Providing Entertainment For All Occasions
555 274 9160
silverharborrhythm@mailnest.net
silverharborrhythm.net

```html
<!DOCTYPE html>
<html lang="en">
<head>
<meta charset="utf-8">
<title>Silver Harbor Rhythm – Business Card</title>
<link href="https://fonts.googleapis.com/css2?family=Open+Sans:wght@400;600;700&display=swap" rel="stylesheet">
<style>
  :root {
    --bg: #e9e6e1;
    --card: #ffffff;
    --green: #1f3d14;
    --green-mid: #2f5a1f;
    --red: #b3262a;
    --text: #4a4a4a;
    --text-dark: #333333;
    --rule: #9a9a9a;
  }
  * { margin: 0; padding: 0; box-sizing: border-box; }
  html, body {
    width: 1200px; height: 829px; overflow: hidden;
    background: var(--bg);
    font-family: "Open Sans", Arial, sans-serif;
  }
  .stage {
    width: 1200px; height: 829px;
    display: flex; align-items: center; justify-content: center; gap: 40px;
  }
  .card {
    position: relative;
    width: 540px; height: 309px;
    background: var(--card);
    box-shadow: 0 6px 18px rgba(0,0,0,0.18);
    overflow: hidden;
  }
  /* brand name lockup */
  .brand {
    display: flex; align-items: center; justify-content: center; gap: 10px;
    color: var(--green);
    font-weight: 700;
    letter-spacing: 0.5px;
  }
  .brand-mark {
    width: 14px; height: 14px; border-radius: 50%;
    background: var(--red);
  }
  /* contact side */
  .card--contact .brand {
    position: absolute; top: 46px; left: 0; right: 0;
    font-size: 24px;
  }
  .name-band {
    position: absolute; left: 0; right: 0; top: 120px; height: 38px;
    background: var(--green);
    border-top: 3px solid var(--card);
    border-bottom: 3px solid var(--card);
    outline: 2px solid var(--green);
    display: flex; align-items: center;
    padding-left: 120px;
    color: #fff; font-size: 16px; font-weight: 700;
  }
  .name-band .title { font-weight: 400; }
  .details {
    position: absolute; top: 176px; left: 0; right: 0;
    display: flex; justify-content: center;
  }
  .address {
    width: 200px; padding-right: 18px;
    text-align: right; color: var(--text); font-size: 13px; line-height: 20px;
    padding-top: 10px;
  }
  .divider { width: 1px; height: 72px; background: var(--rule); }
  .contacts {
    list-style: none; padding-left: 16px;
    color: var(--text); font-size: 12px; line-height: 22px;
  }
  .contacts li { display: flex; align-items: center; gap: 8px; }
  .contacts svg { width: 13px; height: 13px; flex: none; }
  .base-band {
    position: absolute; left: 0; right: 0; bottom: 22px; height: 16px;
    background: var(--green);
    border-top: 3px solid var(--card);
    border-bottom: 3px solid var(--card);
    outline: 2px solid var(--green);
  }
  /* brand side */
  .card--brand {
    display: flex; flex-direction: column; align-items: center; justify-content: center; gap: 26px;
  }
  .card--brand .brand { font-size: 32px; }
  .card--brand .brand-mark { width: 18px; height: 18px; }
  .website { color: var(--text-dark); font-size: 19px; letter-spacing: 0.5px; }
</style>
</head>
<body>
<main class="stage">
  <section class="card card--contact">
    <div class="brand"><span class="brand-mark"></span>Silver Harbor Rhythm</div>
    <div class="name-band"><span>Your Name,&nbsp;</span><span class="title">Title</span></div>
    <div class="details">
      <p class="address">Sreet Name, City Name<br>Zip Code-00000</p>
      <span class="divider"></span>
      <ul class="contacts">
        <li>
          <svg viewBox="0 0 16 16" aria-hidden="true"><circle cx="8" cy="8" r="8" fill="#2f5a1f"/><path d="M5.2 4.2l1.4-.2.8 2-1 .8a5 5 0 0 0 2.8 2.8l.8-1 2 .8-.2 1.4c-3.6.4-7-3-6.6-6.6z" fill="#fff"/></svg>
          555 274 9160
        </li>
        <li>
          <svg viewBox="0 0 16 16" aria-hidden="true"><circle cx="8" cy="8" r="8" fill="#2f5a1f"/><rect x="4" y="5" width="8" height="6" fill="#fff"/><path d="M4 5l4 3.5L12 5" fill="none" stroke="#2f5a1f" stroke-width="1"/></svg>
          silverharborrhythm@mailnest.net
        </li>
        <li>
          <svg viewBox="0 0 16 16" aria-hidden="true"><circle cx="8" cy="8" r="8" fill="#2f5a1f"/><circle cx="8" cy="8" r="4.5" fill="none" stroke="#fff" stroke-width="1"/><path d="M3.5 8h9M8 3.5c-2 2.5-2 6.5 0 9M8 3.5c2 2.5 2 6.5 0 9" fill="none" stroke="#fff" stroke-width="0.9"/></svg>
          www.silverharborrhythm.net
        </li>
      </ul>
    </div>
    <div class="base-band"></div>
  </section>

  <section class="card card--brand">
    <div class="brand"><span class="brand-mark"></span>Silver Harbor Rhythm</div>
    <p class="website">www.silverharborrhythm.net</p>
  </section>
</main>
</body>
</html>
```